Coastal Learner Bureau business cards

Australian company about to start offering its services. We recruit international students to come to study English, vocational education and postgraduate courses in Australia. We help them find the institution and select the right city they want to come to Australia. We are a young, online oriented and supportive agency. Our clients are between 18 and 35 years old, mainly University students, young professionals or people with work experience. We provide much more information that any other agency offer. We administrate a Facebook group with more than 11.000 members that daily ask questions about general information when coming to Australia, while they are here and even after they leave the country

Target Market(s)

International students from South America, Central America and Europe

Industry/Entity Type

Student

Contact Information for Business Card

Tomas Bilbrea
Managing Director
tomas@kelvarin.com.au
www.kelvoria.com.au
+61 491058264
Melbourne, Australia

Font styles to use
Serif
Sans Serif

Colors

Designer to choose colors to be used in the design.

Requirements
Must have
• Horizontal design
• Standard business card size and shape. If font uses green or yellow colours, they will have to match the ones from the logo
Nice to have
• UPDATE: Use the contents of the green image to design one of the card sides. Use our logo in the background of that side as watermark.
• Passport image, or immigration stamps. A picture of the Yarra River (from Melbourne) would be cool as well.
Should not have
• Non-standard business card size and shape
• Not black as the background colour of any sides as we are not a VIP agency or a hight class service. We are orientes to young people and they like colours, pictures, something attractive.
• Vertical design
• NO YELLOW or BLACK AS THE BACKGROUND COLOUR OF ANY SIDE OF THE BIZ CARD

```html
<!DOCTYPE html>
<html lang="en">
<head>
<meta charset="utf-8">
<title>Tomas Bilbrea – Business Card</title>
<link rel="stylesheet" href="https://fonts.googleapis.com/css2?family=EB+Garamond:ital,wght@0,500;0,700;1,400&display=swap">
<style>
  :root {
    --card-white: #ffffff;
    --ink-brown: #8a5a36;
    --ink-brown-soft: #8d603f;
    --watermark-grey: rgba(120, 120, 120, 0.22);
    --sky-top: #6f9fc9;
    --city-mid: #9aa9b4;
    --river-low: #6f7f8c;
  }
  * { margin: 0; padding: 0; box-sizing: border-box; }
  html, body {
    width: 1200px;
    height: 686px;
    overflow: hidden;
    background: var(--card-white);
  }
  .business-card {
    position: relative;
    width: 1200px;
    height: 686px;
    overflow: hidden;
    font-family: "EB Garamond", Garamond, serif;
  }
  .river-photo {
    position: absolute;
    inset: 0;
    background: linear-gradient(180deg, var(--sky-top) 0%, var(--city-mid) 45%, var(--river-low) 100%);
  }
  .content-panel {
    position: absolute;
    left: 18px;
    top: 32px;
    width: 1164px;
    height: 574px;
    background: var(--card-white);
  }
  .brand-watermark {
    position: absolute;
    left: 0;
    right: 0;
    top: 262px;
    text-align: center;
    font-size: 150px;
    font-weight: 700;
    line-height: 1;
    color: var(--watermark-grey);
    letter-spacing: 2px;
  }
  .identity {
    position: absolute;
    left: 0;
    right: 0;
    top: 150px;
    text-align: center;
  }
  .person-name {
    font-size: 68px;
    font-weight: 700;
    line-height: 1;
    color: var(--ink-brown);
  }
  .person-role {
    margin-top: 16px;
    font-size: 42px;
    font-weight: 700;
    line-height: 1;
    color: var(--ink-brown);
  }
  .contact-list {
    list-style: none;
    margin-top: 44px;
    font-size: 34px;
    font-style: italic;
    font-weight: 400;
    line-height: 44px;
    color: var(--ink-brown-soft);
  }
</style>
</head>
<body>
  <main class="business-card">
    <div class="river-photo" role="img" aria-label="Photograph of the Yarra River and Melbourne city skyline"></div>
    <section class="content-panel">
      <div class="brand-watermark" aria-hidden="true">Kelvoria</div>
      <div class="identity">
        <h1 class="person-name">Tomas Bilbrea</h1>
        <p class="person-role">Managing Director</p>
        <ul class="contact-list">
          <li>email: tomas@kelvarin.com.au</li>
          <li>Tel: +61 491058264</li>
          <li>Melbourne, Australia</li>
          <li>web: www.kelvoria.com.au</li>
        </ul>
      </div>
    </section>
  </main>
</body>
</html>
```